Heron Loan Partners Business Card

We need a business card design for our mortgage servicing company. In addition to servicing the loans of homeowners, we help homeowners with purchasing their homes and any mortgage refinancing. We would like to see designs that use the colors in the logo attached below (gold-ish yellow and navy blue), and any other design you deem fit! The design should communicate a simpler life with smart mortgages provided by Heron.

```html
<!DOCTYPE html>
<html lang="en">
<head>
<meta charset="utf-8">
<title>Heron Loan Partners – Business Card</title>
<link rel="stylesheet" href="https://fonts.googleapis.com/css2?family=Montserrat:wght@500;700&family=Open+Sans:wght@400;600&display=swap">
<style>
  :root {
    --gold: #e0b23f;
    --navy: #1f1d5c;
    --ink: #111111;
    --paper: #ffffff;
    --backdrop: #242427;
  }
  * { box-sizing: border-box; margin: 0; padding: 0; }
  html, body {
    width: 1200px; height: 780px; overflow: hidden;
    background: var(--backdrop);
  }
  .sheet {
    width: 1200px; height: 780px;
    display: flex; align-items: center; justify-content: center; gap: 40px;
  }
  .card {
    position: relative;
    width: 540px; height: 309px;
    overflow: hidden;
  }
  .card-front { background: var(--gold); }
  .card-back { background: var(--paper); }

  .brand {
    position: absolute;
    display: flex; align-items: center; gap: 12px;
    font-family: "Montserrat", sans-serif;
    font-weight: 700;
    color: var(--navy);
    white-space: nowrap;
  }
  .brand-dot {
    width: 18px; height: 18px; border-radius: 50%;
    background: var(--navy);
    flex: none;
  }
  .card-front .brand {
    left: 50%; top: 50%; transform: translate(-50%, -50%);
    font-size: 34px;
  }
  .card-back .brand {
    left: 60px; top: 62px;
    font-size: 26px;
  }
  .card-back .brand .brand-dot { width: 14px; height: 14px; }

  .person {
    position: absolute; left: 60px; top: 160px;
    font-family: "Montserrat", sans-serif;
  }
  .person-name { font-size: 27px; font-weight: 700; color: var(--ink); letter-spacing: 0.3px; }
  .person-name .first { color: var(--gold); }
  .person-role { font-size: 14px; font-weight: 500; color: var(--ink); margin-top: 4px; }

  .divider {
    position: absolute; left: 310px; top: 128px;
    width: 1px; height: 100px; background: var(--ink);
  }

  .contact {
    position: absolute; left: 330px; top: 140px;
    list-style: none;
    font-family: "Open Sans", sans-serif;
    font-size: 13.5px; color: var(--ink);
  }
  .contact li { display: flex; align-items: center; gap: 9px; line-height: 26px; }
  .contact svg { width: 13px; height: 13px; flex: none; fill: var(--gold); }

  .address-band {
    position: absolute; left: 0; right: 0; bottom: 16px; height: 38px;
    background: var(--gold);
    display: flex; align-items: center; justify-content: center;
    font-family: "Open Sans", sans-serif; font-size: 14px; font-weight: 600;
    color: var(--paper); letter-spacing: 0.3px;
  }
</style>
</head>
<body>
<main class="sheet">
  <section class="card card-front" aria-label="Card front">
    <div class="brand"><span class="brand-dot"></span>Heron Loan Partners</div>
  </section>

  <section class="card card-back" aria-label="Card back">
    <div class="brand"><span class="brand-dot"></span>Heron Loan Partners</div>

    <div class="person">
      <p class="person-name"><span class="first">Lena</span> Varga</p>
      <p class="person-role">Managing Director</p>
    </div>

    <div class="divider"></div>

    <ul class="contact">
      <li>
        <svg viewBox="0 0 24 24" aria-hidden="true"><path d="M6.6 10.8a15.1 15.1 0 0 0 6.6 6.6l2.2-2.2a1 1 0 0 1 1-.25 11.4 11.4 0 0 0 3.6.57 1 1 0 0 1 1 1V20a1 1 0 0 1-1 1A17 17 0 0 1 3 4a1 1 0 0 1 1-1h3.5a1 1 0 0 1 1 1c0 1.25.2 2.45.57 3.6a1 1 0 0 1-.25 1z"/></svg>
        (555) 214-0387
      </li>
      <li>
        <svg viewBox="0 0 24 24" aria-hidden="true"><path d="M2 5h20v14H2zm2 2v.5l8 5 8-5V7zm0 2.9V17h16V9.9l-8 5z"/></svg>
        info@heronloans.com
      </li>
      <li>
        <svg viewBox="0 0 24 24" aria-hidden="true"><path d="M12 2a10 10 0 1 0 0 20 10 10 0 0 0 0-20zm6.9 6h-2.9a15.7 15.7 0 0 0-1.4-3.6A8 8 0 0 1 18.9 8zM12 4c.8 1.2 1.5 2.5 1.9 4h-3.8c.4-1.5 1.1-2.8 1.9-4zM4.3 14a8 8 0 0 1 0-4h3.4a16.5 16.5 0 0 0 0 4zm.8 2h2.9c.3 1.3.8 2.5 1.4 3.6A8 8 0 0 1 5.1 16zM8 8H5.1a8 8 0 0 1 4.3-3.6C8.8 5.5 8.3 6.7 8 8zm4 12c-.8-1.2-1.5-2.5-1.9-4h3.8c-.4 1.5-1.1 2.8-1.9 4zm2.3-6H9.7a14.7 14.7 0 0 1 0-4h4.6a14.7 14.7 0 0 1 0 4zm.3 5.6c.6-1.1 1.1-2.3 1.4-3.6h2.9a8 8 0 0 1-4.3 3.6zm1.7-5.6a16.5 16.5 0 0 0 0-4h3.4a8 8 0 0 1 0 4z"/></svg>
        www.heronloans.com
      </li>
    </ul>

    <div class="address-band">2480 Calloway Ct #204, Ridgefield, FL 32901, USA</div>
  </section>
</main>
</body>
</html>
```